Building company needs a letterhead design

I'm after a modern but professional letter head.
Must have the below details:
- Logo
- Website - TARVELLGROUP.COM.AU
- Email - INFO@TARVELLGROUP.COM.AU
- Office - 03 57263018
- Mobile number - 0418536294
- ABN - 47 315 962 108
...........................................................................................................................................................................................................................
- Logo
- Office - 03 57263018
- ABN - 47 315 962 108

Target Market(s)

.

Industry/Entity Type

Construction Company

Font styles to use
Sans Serif

Requirements
Must have
• Must have the below details:
• - Logo
• - Website - TARVELLGROUP.COM.AU
• - Email - INFO@TARVELLGROUP.COM.AU
• - Office - 03 57263018
• - Mobile number - 0418536294
• - ABN - 47 315 962 108
Nice to have
• .
Should not have
• .

```html
<!DOCTYPE html>
<html lang="en">
<head>
<meta charset="utf-8">
<title>Tarvell Building Group – Letterhead</title>
<link rel="stylesheet" href="https://fonts.googleapis.com/css2?family=Open+Sans:wght@400;700&display=swap">
<style>
  :root {
    --backdrop: #e9e6e1;
    --paper: #ffffff;
    --brand-yellow: #f5b31b;
    --rule-grey: #77787b;
    --text-grey: #5a5b5e;
    --ghost: #f3f1ec;
  }
  * { box-sizing: border-box; margin: 0; padding: 0; }
  html, body {
    width: 1186px; height: 1200px; overflow: hidden;
    background: var(--backdrop);
    font-family: "Open Sans", Arial, sans-serif;
  }
  .letterhead {
    position: absolute; left: 197px; top: 40px;
    width: 792px; height: 1120px;
    background: var(--paper);
    box-shadow: 0 4px 18px rgba(0,0,0,0.18);
  }
  .brand {
    position: absolute; left: 48px; top: 52px;
    display: flex; align-items: center; gap: 12px;
  }
  .brand-square {
    width: 34px; height: 34px; background: var(--brand-yellow);
  }
  .brand-name {
    font-weight: 700; font-size: 24px; letter-spacing: 1.5px;
    color: var(--brand-yellow); line-height: 1;
  }
  .header-rule {
    position: absolute; left: 0; top: 118px;
    width: 560px; height: 2px; background: var(--rule-grey);
  }
  .header-rule-end {
    position: absolute; right: 0; top: 146px;
    width: 40px; height: 2px; background: var(--rule-grey);
  }
  .website {
    position: absolute; right: 56px; top: 126px;
    font-size: 12px; letter-spacing: 1.6px; color: var(--text-grey);
  }
  .ghost-name {
    position: absolute; left: 0; right: 0; top: 520px;
    text-align: center; font-weight: 700; font-size: 60px;
    letter-spacing: 4px; color: var(--ghost);
  }
  .contact-bar {
    position: absolute; left: 48px; bottom: 44px;
    display: flex; align-items: center; gap: 14px;
    font-size: 11px; color: var(--text-grey);
  }
  .contact-item { display: flex; align-items: center; gap: 5px; }
  .contact-item svg { width: 11px; height: 11px; fill: var(--text-grey); }
  .divider { color: var(--rule-grey); }
</style>
</head>
<body>
  <main class="letterhead">
    <header>
      <div class="brand">
        <span class="brand-square"></span>
        <span class="brand-name">TARVELL BUILDING GROUP</span>
      </div>
      <div class="header-rule"></div>
      <span class="website">www.tarvellgroup.com.au</span>
      <div class="header-rule-end"></div>
    </header>

    <div class="ghost-name" aria-hidden="true">TARVELL</div>

    <footer class="contact-bar">
      <span class="contact-item">
        <svg viewBox="0 0 24 24"><path d="M6.6 10.8a15 15 0 0 0 6.6 6.6l2.2-2.2a1 1 0 0 1 1-.25 11.4 11.4 0 0 0 3.6.57 1 1 0 0 1 1 1V20a1 1 0 0 1-1 1A17 17 0 0 1 3 4a1 1 0 0 1 1-1h3.5a1 1 0 0 1 1 1c0 1.25.2 2.45.57 3.57a1 1 0 0 1-.25 1z"/></svg>
        03 57263018
      </span>
      <span class="contact-item">
        <svg viewBox="0 0 24 24"><path d="M7 1h10a2 2 0 0 1 2 2v18a2 2 0 0 1-2 2H7a2 2 0 0 1-2-2V3a2 2 0 0 1 2-2zm0 4v13h10V5z"/></svg>
        0418536294
      </span>
      <span class="contact-item">
        <svg viewBox="0 0 24 24"><path d="M2 5h20v14H2zm2 2v.5l8 5 8-5V7z"/></svg>
        info@tarvellgroup.com.au
      </span>
      <span class="divider">|</span>
      <span class="contact-item">ABN: 47 315 962 108</span>
    </footer>
  </main>
</body>
</html>
```